Webdesign für Projektmanagement
Zielgruppe
Projektmanagement und Projektsteuerung von Bauvorhaben für Projektentwickler und Bauträger.
Wesentliche Bereiche sind Wirtschaftliche Steuerung, Steuerung der Baustelle und Bauabläufe sowie Steuerung der Marketing und Vertriebsaktivitäten.
Aufgabenstellung
Orientierung am Logo. Logo und Visitenkarte liegen bei. Schriftart Prelo und Prelo Slab.

```html
<!DOCTYPE html>
<html lang="de">
<head>
<meta charset="utf-8">
<title>Vallstein – Projektmanagement</title>
<link href="https://fonts.googleapis.com/css2?family=Raleway:ital,wght@0,300;0,400;0,500;0,600;1,400&family=Roboto+Slab:wght@700&display=swap" rel="stylesheet">
<style>
:root{
  --navy:#0a2541;
  --stage:#07223d;
  --gold:#a99148;
  --white:#ffffff;
  --card:#f1f1f1;
  --text:#2c2c2c;
  --muted:#6d6d6d;
  --line:#ececec;
}
*{margin:0;padding:0;box-sizing:border-box}
html,body{width:701px;height:1200px;overflow:hidden}
body{background:var(--stage);font-family:"Raleway",sans-serif;position:relative}
.screen{position:absolute;left:20px;width:663px;height:381px;display:flex}
.screen--one{top:12px}
.screen--two{top:409px}
.screen--three{top:806px}
.sidebar{width:101px;height:100%;background:var(--white);position:relative}
.brand{position:absolute;top:44px;left:15px;display:flex;align-items:center;gap:4px}
.brand__mark{width:6px;height:6px;background:var(--gold)}
.brand__name{font-family:"Roboto Slab",serif;font-weight:700;font-size:14px;color:var(--navy);letter-spacing:-.2px}
.nav{position:absolute;top:93px;left:0;width:100%;list-style:none;border-top:1px solid var(--line)}
.nav li{height:20.2px;border-bottom:1px solid var(--line);display:flex;align-items:center;justify-content:space-between;padding:0 11px 0 16px;font-size:5.8px;font-weight:500;color:var(--navy);letter-spacing:.2px}
.nav li.is-active{color:var(--gold);font-weight:600}
.nav .chev{color:var(--muted);font-size:7px}
.nav li.search{justify-content:flex-start;gap:5px;font-style:italic;color:var(--muted);font-weight:400;text-transform:none}
.social{position:absolute;top:361px;left:23px;display:flex;gap:7px}
.social span{width:6px;height:6px;border-radius:50%;background:var(--navy)}
.hero{flex:1;position:relative;overflow:hidden}
.hero__photo{position:absolute;inset:0}
.screen--one .hero__photo{background:linear-gradient(135deg,#d9c473 0%,#d6c89a 35%,#c8b780 60%,#b99f5c 100%)}
.screen--two .hero__photo{background:linear-gradient(120deg,#a89a63 0%,#b6a46a 40%,#c2ad63 65%,#a99a66 100%)}
.screen--three .hero__photo{background:linear-gradient(135deg,#b4a265 0%,#ad9c63 45%,#a8975f 100%)}
.topbar{position:absolute;top:7px;left:35px;display:flex;gap:11px;font-size:5.3px;color:var(--white);align-items:center}
.topbar span{display:flex;align-items:center;gap:3px}
.kicker{position:absolute;top:100px;left:35px;font-size:9.6px;font-weight:600;color:var(--gold);letter-spacing:.1px}
.screen--two .kicker,.screen--three .kicker{color:#9c8b4f}
.headline{position:absolute;top:124px;left:34px;font-size:33px;font-weight:300;line-height:38px;color:var(--white);letter-spacing:.6px}
.card{position:absolute;top:226px;width:132px;height:93px;background:var(--card);padding:6px 8px 0}
.card--a{left:35px}.card--b{left:173px}.card--c{left:311px}
.card__cat{font-size:5.3px;font-style:italic;color:var(--muted)}
.card__title{margin-top:4px;font-size:6.3px;line-height:8.5px;font-weight:500;color:var(--gold)}
.card__body{margin-top:4px;font-size:5.3px;line-height:8.5px;color:var(--text)}
.card__btn{position:absolute;right:0;bottom:0;width:51px;height:13px;background:var(--navy);color:var(--white);font-size:4.8px;font-weight:600;display:flex;align-items:center;justify-content:center;letter-spacing:.2px}
.footer{position:absolute;top:368px;left:35px;font-size:5.3px;color:var(--white)}
</style>
</head>
<body>

<section class="screen screen--one">
  <aside class="sidebar">
    <div class="brand"><span class="brand__name">Vallstein</span><span class="brand__mark"></span></div>
    <ul class="nav">
      <li class="is-active">HOME</li><li>LEISTUNGEN</li><li>ÜBER UNS <span class="chev">›</span></li><li>PROJEKTE <span class="chev">›</span></li><li>PARTNER</li><li>KONTAKT</li>
      <li class="search"><svg width="5" height="5" viewBox="0 0 10 10"><circle cx="4" cy="4" r="3" fill="none" stroke="#a99148" stroke-width="1.6"/><line x1="6.3" y1="6.3" x2="9.5" y2="9.5" stroke="#a99148" stroke-width="1.6"/></svg>Suchen</li>
    </ul>
    <div class="social"><span></span><span></span><span></span><span></span></div>
  </aside>
  <main class="hero">
    <div class="hero__photo" role="img" aria-label="Foto: Bauhelm, Baupläne, Taschenrechner und Holzbauklötze auf einem Schreibtisch, gelb getönt"></div>
    <div class="topbar">
      <span><svg width="5" height="5" viewBox="0 0 10 10"><path d="M2 1l2 2-1 1.5c.8 1.5 1.5 2.2 3 3L7.5 6l2 2-1.5 1.5C4 9 1 6 .5 1.5z" fill="#a99148"/></svg>+49 (0)211 - 000 123 45</span>
      <span><svg width="5" height="5" viewBox="0 0 10 10"><circle cx="5" cy="5" r="4" fill="none" stroke="#a99148" stroke-width="1.2"/><path d="M5 2.5V5h2" fill="none" stroke="#a99148" stroke-width="1.2"/></svg>Mo - Fr 9:00 - 18:00</span>
      <span><svg width="6" height="5" viewBox="0 0 12 9"><rect x=".5" y=".5" width="11" height="8" fill="none" stroke="#a99148"/><path d="M.5.5l5.5 4.5L11.5.5" fill="none" stroke="#a99148"/></svg>info@vallstein.de</span>
      <span><svg width="4" height="6" viewBox="0 0 8 12"><path d="M4 0a4 4 0 014 4c0 3-4 8-4 8S0 7 0 4a4 4 0 014-4z" fill="#a99148"/><circle cx="4" cy="4" r="1.5" fill="#fff"/></svg>Beispielweg 12, 40210 Düsseldorf</span>
    </div>
    <div class="kicker">PROJEKTMANAGEMENT &amp; PROJEKTSTEUERUNG</div>
    <h1 class="headline">WIR REALISIEREN<br>BAUVORHABEN</h1>
    <article class="card card--a"><p class="card__cat">Betriebswirtschaftliche Planung</p><h2 class="card__title">STET CLITA KASD GUBERGREN NO SEA TAKIMATA SANCTUS EST LOREM</h2><p class="card__body">Lorem ipsum dolor sit amet, consetetur sadipscing elitr, sed diam nonumy eirmod tempor invidunt ut labore et dolore magna aliquyam erat, sed diam voluptua.</p><span class="card__btn">WEITERLESEN</span></article>
    <article class="card card--b"><p class="card__cat">Steuerung der baulichen Umsetzung</p><h2 class="card__title">STET CLITA KASD GUBERGREN NO SEA TAKIMATA SANCTUS EST LOREM</h2><p class="card__body">Lorem ipsum dolor sit amet, consetetur sadipscing elitr, sed diam nonumy eirmod tempor invidunt ut labore et dolore magna aliquyam erat, sed diam voluptua.</p><span class="card__btn">WEITERLESEN</span></article>
    <article class="card card--c"><p class="card__cat">Marketing und Vertrieb</p><h2 class="card__title">STET CLITA KASD GUBERGREN NO SEA TAKIMATA SANCTUS EST LOREM</h2><p class="card__body">Lorem ipsum dolor sit amet, consetetur sadipscing elitr, sed diam nonumy eirmod tempor invidunt ut labore et dolore magna aliquyam erat, sed diam voluptua.</p><span class="card__btn">WEITERLESEN</span></article>
    <p class="footer">© 2017 Vallstein Immobilien GmbH - Impressum</p>
  </main>
</section>

<section class="screen screen--two">
  <aside class="sidebar">
    <div class="brand"><span class="brand__name">Vallstein</span><span class="brand__mark"></span></div>
    <ul class="nav">
      <li class="is-active">HOME</li><li>LEISTUNGEN</li><li>ÜBER UNS <span class="chev">›</span></li><li>PROJEKTE <span class="chev">›</span></li><li>PARTNER</li><li>KONTAKT</li>
      <li class="search"><svg width="5" height="5" viewBox="0 0 10 10"><circle cx="4" cy="4" r="3" fill="none" stroke="#a99148" stroke-width="1.6"/><line x1="6.3" y1="6.3" x2="9.5" y2="9.5" stroke="#a99148" stroke-width="1.6"/></svg>Suchen</li>
    </ul>
    <div class="social"><span></span><span></span><span></span><span></span></div>
  </aside>
  <main class="hero">
    <div class="hero__photo" role="img" aria-label="Foto: Bauhelm, Laptop mit Gebäudemodell und Messgerät auf einem Tisch, goldfarben getönt"></div>
    <div class="topbar">
      <span><svg width="5" height="5" viewBox="0 0 10 10"><path d="M2 1l2 2-1 1.5c.8 1.5 1.5 2.2 3 3L7.5 6l2 2-1.5 1.5C4 9 1 6 .5 1.5z" fill="#a99148"/></svg>+49 (0)211 - 000 123 45</span>
      <span><svg width="5" height="5" viewBox="0 0 10 10"><circle cx="5" cy="5" r="4" fill="none" stroke="#a99148" stroke-width="1.2"/><path d="M5 2.5V5h2" fill="none" stroke="#a99148" stroke-width="1.2"/></svg>Mo - Fr 9:00 - 18:00</span>
      <span><svg width="6" height="5" viewBox="0 0 12 9"><rect x=".5" y=".5" width="11" height="8" fill="none" stroke="#a99148"/><path d="M.5.5l5.5 4.5L11.5.5" fill="none" stroke="#a99148"/></svg>info@vallstein.de</span>
      <span><svg width="4" height="6" viewBox="0 0 8 12"><path d="M4 0a4 4 0 014 4c0 3-4 8-4 8S0 7 0 4a4 4 0 014-4z" fill="#a99148"/><circle cx="4" cy="4" r="1.5" fill="#fff"/></svg>Beispielweg 12, 40210 Düsseldorf</span>
    </div>
    <div class="kicker">PROJEKTMANAGEMENT &amp; PROJEKTSTEUERUNG</div>
    <h1 class="headline">WIR REALISIEREN<br>BAUVORHABEN</h1>
    <article class="card card--a"><p class="card__cat">Betriebswirtschaftliche Planung</p><h2 class="card__title">STET CLITA KASD GUBERGREN NO SEA TAKIMATA SANCTUS EST LOREM</h2><p class="card__body">Lorem ipsum dolor sit amet, consetetur sadipscing elitr, sed diam nonumy eirmod tempor invidunt ut labore et dolore magna aliquyam erat, sed diam voluptua.</p><span class="card__btn">WEITERLESEN</span></article>
    <article class="card card--b"><p class="card__cat">Steuerung der baulichen Umsetzung</p><h2 class="card__title">STET CLITA KASD GUBERGREN NO SEA TAKIMATA SANCTUS EST LOREM</h2><p class="card__body">Lorem ipsum dolor sit amet, consetetur sadipscing elitr, sed diam nonumy eirmod tempor invidunt ut labore et dolore magna aliquyam erat, sed diam voluptua.</p><span class="card__btn">WEITERLESEN</span></article>
    <article class="card card--c"><p class="card__cat">Marketing und Vertrieb</p><h2 class="card__title">STET CLITA KASD GUBERGREN NO SEA TAKIMATA SANCTUS EST LOREM</h2><p class="card__body">Lorem ipsum dolor sit amet, consetetur sadipscing elitr, sed diam nonumy eirmod tempor invidunt ut labore et dolore magna aliquyam erat, sed diam voluptua.</p><span class="card__btn">WEITERLESEN</span></article>
    <p class="footer">© 2017 Vallstein Immobilien GmbH - Impressum</p>
  </main>
</section>

<section class="screen screen--three">
  <aside class="sidebar">
    <div class="brand"><span class="brand__name">Vallstein</span><span class="brand__mark"></span></div>
    <ul class="nav">
      <li class="is-active">HOME</li><li>LEISTUNGEN</li><li>ÜBER UNS <span class="chev">›</span></li><li>PROJEKTE <span class="chev">›</span></li><li>PARTNER</li><li>KONTAKT</li>
      <li class="search"><svg width="5" height="5" viewBox="0 0 10 10"><circle cx="4" cy="4" r="3" fill="none" stroke="#a99148" stroke-width="1.6"/><line x1="6.3" y1="6.3" x2="9.5" y2="9.5" stroke="#a99148" stroke-width="1.6"/></svg>Suchen</li>
    </ul>
    <div class="social"><span></span><span></span><span></span><span></span></div>
  </aside>
  <main class="hero">
    <div class="hero__photo" role="img" aria-label="Foto: Grundrisspläne mit Taschenrechner und Lineal, goldfarben getönt"></div>
    <div class="topbar">
      <span><svg width="5" height="5" viewBox="0 0 10 10"><path d="M2 1l2 2-1 1.5c.8 1.5 1.5 2.2 3 3L7.5 6l2 2-1.5 1.5C4 9 1 6 .5 1.5z" fill="#a99148"/></svg>+49 (0)211 - 000 123 45</span>
      <span><svg width="5" height="5" viewBox="0 0 10 10"><circle cx="5" cy="5" r="4" fill="none" stroke="#a99148" stroke-width="1.2"/><path d="M5 2.5V5h2" fill="none" stroke="#a99148" stroke-width="1.2"/></svg>Mo - Fr 9:00 - 18:00</span>
      <span><svg width="6" height="5" viewBox="0 0 12 9"><rect x=".5" y=".5" width="11" height="8" fill="none" stroke="#a99148"/><path d="M.5.5l5.5 4.5L11.5.5" fill="none" stroke="#a99148"/></svg>info@vallstein.de</span>
      <span><svg width="4" height="6" viewBox="0 0 8 12"><path d="M4 0a4 4 0 014 4c0 3-4 8-4 8S0 7 0 4a4 4 0 014-4z" fill="#a99148"/><circle cx="4" cy="4" r="1.5" fill="#fff"/></svg>Beispielweg 12, 40210 Düsseldorf</span>
    </div>
    <div class="kicker">PROJEKTMANAGEMENT &amp; PROJEKTSTEUERUNG</div>
    <h1 class="headline">WIR REALISIEREN<br>BAUVORHABEN</h1>
    <article class="card card--a"><p class="card__cat">Betriebswirtschaftliche Planung</p><h2 class="card__title">STET CLITA KASD GUBERGREN NO SEA TAKIMATA SANCTUS EST LOREM</h2><p class="card__body">Lorem ipsum dolor sit amet, consetetur sadipscing elitr, sed diam nonumy eirmod tempor invidunt ut labore et dolore magna aliquyam erat, sed diam voluptua.</p><span class="card__btn">WEITERLESEN</span></article>
    <article class="card card--b"><p class="card__cat">Steuerung der baulichen Umsetzung</p><h2 class="card__title">STET CLITA KASD GUBERGREN NO SEA TAKIMATA SANCTUS EST LOREM</h2><p class="card__body">Lorem ipsum dolor sit amet, consetetur sadipscing elitr, sed diam nonumy eirmod tempor invidunt ut labore et dolore magna aliquyam erat, sed diam voluptua.</p><span class="card__btn">WEITERLESEN</span></article>
    <article class="card card--c"><p class="card__cat">Marketing und Vertrieb</p><h2 class="card__title">STET CLITA KASD GUBERGREN NO SEA TAKIMATA SANCTUS EST LOREM</h2><p class="card__body">Lorem ipsum dolor sit amet, consetetur sadipscing elitr, sed diam nonumy eirmod tempor invidunt ut labore et dolore magna aliquyam erat, sed diam voluptua.</p><span class="card__btn">WEITERLESEN</span></article>
    <p class="footer">© 2017 Vallstein Immobilien GmbH - Impressum</p>
  </main>
</section>

</body>
</html>
```